Brochure design - tarrow floors

i need a brochure design for my flooring business which is in the same style/theme as the attached file. the images chosen from framequarry should be focused on quality flooring and presented in a corporate and professional way. this design will be intended for printed brochures which i can hand to my clients as part of the sales process... I have a logo which should be included into the design (attached)
Requirements
Must have
- This design should be ready for "Z" folded leaflet format - similar to the file attached
The design should present the images i attached in the brief
the design should follow the theme of the attached complete, sample brochure
the design needs to present the attached company logo in a clear and impressive way.
the design should allow for text boxes near each of the images

```html
<!DOCTYPE html>
<html lang="en">
<head>
<meta charset="utf-8">
<title>Tarrow Floors – Z-fold brochure</title>
<link rel="stylesheet" href="https://fonts.googleapis.com/css2?family=Nunito+Sans:wght@300;400;700&display=swap">
<style>
  :root{
    --page:#ffffff;
    --teal:#3fb3d0;
    --teal-deep:#0f3540;
    --teal-photo:#5aaec6;
    --brown-box:#2b2118;
    --wood:#b8926c;
    --wood-light:#d8c2a6;
    --mist:#e4ddd6;
    --slate:#4d4f52;
    --charcoal:#3c3c3e;
    --card:#111112;
    --card-grey:#4c5159;
    --ink-light:#f2f2f2;
    --ink-dark:#e8e8e8;
  }
  *{box-sizing:border-box;margin:0;padding:0}
  html,body{width:1200px;height:1200px;overflow:hidden;background:var(--page)}
  body{position:relative;font-family:"Nunito Sans",Arial,sans-serif;font-weight:300;color:var(--ink-light)}
  .spread{position:absolute;left:227px;width:752px;height:531px;overflow:hidden;box-shadow:0 6px 14px rgba(0,0,0,.28)}
  .spread--outer{top:59px}
  .spread--inner{top:622px;background:var(--charcoal)}
  .spread svg.backdrop{position:absolute;inset:0;width:752px;height:531px}
  .box{position:absolute}
  .intro-box{left:26px;top:107px;width:200px;height:424px;background:rgba(10,40,48,.9);padding:22px 24px 0 26px}
  .story-box{left:275px;top:0;width:203px;height:356px;background:rgba(40,30,22,.92);padding:134px 12px 0 26px}
  .contact-box{left:275px;top:371px;width:203px;height:160px;background:rgba(232,226,220,.85);text-align:center}
  .heading{font-weight:300;color:var(--teal);font-size:14.5px;line-height:1;letter-spacing:.1px}
  .copy{font-size:6.6px;line-height:8.5px;color:var(--ink-light)}
  .copy p{margin-top:8.5px}
  .story-box .copy p:first-child{margin-top:0}
  .brand{position:absolute;left:0;right:0;display:flex;flex-direction:column;align-items:center;color:var(--teal);font-weight:300}
  .brand-mark{border:1px solid var(--teal)}
  .contact-box .brand{top:44px}
  .contact-box .brand-mark{width:18px;height:18px;margin-bottom:6px}
  .contact-box .brand-name{font-size:11px;letter-spacing:1px}
  .contact-lines{position:absolute;left:0;right:0;top:118px;font-size:7.6px;line-height:9.5px;font-weight:700;color:var(--teal)}
  .cover-brand{left:568px;width:118px;top:430px;right:auto}
  .cover-brand .brand-mark{width:28px;height:28px;margin-bottom:8px}
  .cover-brand .brand-name{font-size:17px;letter-spacing:1.5px}
  .photo{position:absolute}
  .card{position:absolute;background:var(--card)}
  .card--grey{background:var(--card-grey)}
  .card .photo{left:12px;width:200px}
  .card .heading{position:absolute;left:12px}
  .card .copy{position:absolute;left:12px;width:205px;font-size:6.6px;line-height:8.6px}
  .wood-warm{background:linear-gradient(135deg,#8d6a4a,#d19a58 45%,#c98a44 70%,#cfd8d2)}
  .wood-roll{background:linear-gradient(160deg,#4b3a30,#c79a70 35%,#b48a66 65%,#d9cdb8)}
  .sander{background:linear-gradient(180deg,#d8d8d6,#8a8580 55%,#3a3430)}
  .strip{background:linear-gradient(180deg,#6d6158,#c7b9a6 45%,#2a1c14)}
  .stair{background:linear-gradient(135deg,#e6b57f,#c98540 60%,#f1e7dc)}
</style>
</head>
<body>

<section class="spread spread--outer" aria-label="Brochure outer side">
  <svg class="backdrop" viewBox="0 0 752 531" aria-hidden="false">
    <defs>
      <linearGradient id="woodFloor" x1="0" y1="0" x2="1" y2="1">
        <stop offset="0" stop-color="#a98460"/>
        <stop offset="1" stop-color="#c9a780"/>
      </linearGradient>
      <linearGradient id="tealWash" x1="0" y1="0" x2="0" y2="1">
        <stop offset="0" stop-color="#6db7cc"/>
        <stop offset="1" stop-color="#3f8aa0"/>
      </linearGradient>
      <linearGradient id="coupleTone" x1="0" y1="0" x2="1" y2="1">
        <stop offset="0" stop-color="#cbb196"/>
        <stop offset=".5" stop-color="#a7a4a6"/>
        <stop offset="1" stop-color="#3b4a66"/>
      </linearGradient>
    </defs>
    <rect width="752" height="531" fill="url(#woodFloor)" role="img" aria-label="Photo of an oak wooden floor"/>
    <polygon points="0,0 263,0 225,531 0,531" fill="url(#tealWash)" role="img" aria-label="Teal-toned photo of a bright interior"/>
    <rect x="477" y="0" width="275" height="531" fill="url(#coupleTone)" role="img" aria-label="Photo of a smiling couple lying on a new oak floor"/>
    <polygon points="677,0 752,0 752,190 690,150" fill="#555557" opacity=".85"/>
    <polygon points="477,410 752,256 752,531 477,531" fill="#4d4d4f" opacity=".92"/>
    <g stroke="#ffffff" stroke-width="6" fill="none">
      <line x1="357" y1="0" x2="752" y2="188"/>
      <line x1="260" y1="531" x2="752" y2="256"/>
      <line x1="663" y1="0" x2="726" y2="531"/>
      <line x1="690" y1="150" x2="752" y2="180"/>
    </g>
  </svg>

  <div class="box intro-box">
    <h2 class="heading">Ceariosam volum</h2>
    <div class="copy" style="margin-top:15px">
      <p>As niam nimaximostia venihitat.<br>Harchictis intiore hentotate venet estem harunt dignis nobit aute libus nonsequis si voluptatia cuptae et aut essum nihic tem.</p>
      <p>Odita vent.<br>Picia dias voluptam et et labo. Officid questio eventis est volore aut aligendam, il idem utatur simporepro optaspi distion sequossitas expe consed magnam et volupti onsene velloris sitectore velic to quaspero tenis moloria vel illatio nsequia voloreped que dolorecum ad molupta sperio tessinvel essequa spernatur sequis acerene quaesto consequam litiistiam, sed quiderundi deniam quamet quodia corporit re, consendaerum fuga.</p>
      <p>Ut que nis di as ut eate excerferiam que re labores atur?</p>
      <p>Qui cuscia pra quis voluptae. Nemporae vendae vit ipient dellореriti corestrum lam que a consent.</p>
      <p>Um iusam, volut eic tet quid etur, cusdant.</p>
      <p>Eri iment experio optat optat.<br>Natem sanimaximin endit, voluptatur?</p>
      <p>Ga. Otatquia qui dunt. Unti accus rectibus es cum enis et ilitin essit, asped molum ut hitatur sectorpos escipsam enemus etere moli publicit C. Catanum det in sullere vil viverratum is eto ci casdac mante quem istis ad intea delinti ssunte novidet eatrari catus halariam erei conve, const es ret ac restem publiam, quod condient? P. Cate consulvic iae vivigilin iption dessatu quos tam, que tat ore nonfestuis. Fui praedicer hos cont? Vat, dem cum intissim tem, nes hiliemo iam. Ciis serum. Abem tusulvirit.</p>
    </div>
  </div>

  <div class="box story-box">
    <div class="copy">
      <p>As niam nimaximostia venihitat.<br>Harchictis intiore hentotate venet estem harunt dignis nobit aute li</p>
      <p>bus nonsequis si voluptatia cuptae et aut essum nihic tem. Odita vent.<br>Picia dias voluptam et et labo. Of</p>
      <p>ficid quostio eventis est volore aut aligendam, il idem utatur simporepro optaspi distion sequossitas</p>
      <p>expe consed magnam et volupti onsene velloris sitectore velic to quaspero tenis moloria vel illatio</p>
      <p>nsequia voloreped que dolorecum ad molupta sperio tessinvel essequa spernatur sequis acerene</p>
      <p>quaesto consequam litiistiam, sed quiderundi deniam quamet quodia corporit re, consendaerum</p>
    </div>
  </div>

  <div class="box contact-box">
    <div class="brand">
      <span class="brand-mark"></span>
      <span class="brand-name">tarrow floors</span>
    </div>
    <div class="contact-lines">www.tarrowfloors.co.uk<br>info@tarrowfloors.co.uk</div>
  </div>

  <div class="brand cover-brand">
    <span class="brand-mark"></span>
    <span class="brand-name">tarrow floors</span>
  </div>
</section>

<section class="spread spread--inner" aria-label="Brochure inner side">
  <svg class="backdrop" viewBox="0 0 752 531" aria-hidden="true">
    <polygon points="489,0 752,0 752,531 536,531" fill="var(--teal)"/>
    <g stroke="#8a8a8c" stroke-width="10" opacity=".4" fill="none">
      <line x1="0" y1="191" x2="273" y2="53"/>
      <line x1="0" y1="262" x2="60" y2="285"/>
      <line x1="222" y1="391" x2="488" y2="531"/>
      <line x1="50" y1="270" x2="25" y2="531"/>
    </g>
  </svg>

  <article class="card" style="left:14px;top:0;width:224px;height:266px">
    <div class="photo wood-warm" style="top:0;height:202px" role="img" aria-label="Photo of a fitter marking oak floor boards"></div>
    <h3 class="heading" style="top:211px">Ceariosam volum</h3>
    <p class="copy" style="top:236px">As niam nimaximostia venihitat.<br>Harchictis intiore hentotate venet estem harunt dignis nobit aute libus nonsequis si voluptatia cuptae et aut essum nihic</p>
  </article>
  <article class="card" style="left:14px;top:274px;width:224px;height:257px">
    <div class="photo wood-roll" style="top:12px;height:169px" role="img" aria-label="Photo of a fitter laying a vinyl wood-effect floor"></div>
    <h3 class="heading" style="top:188px">Ceariosam volum</h3>
    <p class="copy" style="top:212px">As niam nimaximostia venihitat.<br>Harchictis intiore hentotate venet estem harunt dignis nobit aute libus nonsequis si voluptatia cuptae et aut essum nihic</p>
  </article>

  <article class="card" style="left:264px;top:0;width:224px;height:120px">
    <div class="photo sander" style="top:0;height:81px" role="img" aria-label="Photo of a floor sanding machine at work"></div>
    <h3 class="heading" style="top:92px">Ceariosam volum</h3>
  </article>
  <article class="card" style="left:264px;top:130px;width:224px;height:128px">
    <div class="photo strip" style="top:9px;height:78px" role="img" aria-label="Photo of a worker stripping an old dark floor"></div>
    <h3 class="heading" style="top:99px">Ceariosam volum</h3>
  </article>
  <article class="card" style="left:264px;top:264px;width:224px;height:122px">
    <div class="photo stair" style="top:2px;height:81px" role="img" aria-label="Photo of a hand sanding a wooden stair tread"></div>
    <h3 class="heading" style="top:94px">Ceariosam volum</h3>
  </article>
  <article class="card" style="left:264px;top:394px;width:224px;height:137px">
    <div class="photo sander" style="top:12px;height:78px" role="img" aria-label="Photo of a floor sanding machine at work"></div>
    <h3 class="heading" style="top:108px">Ceariosam volum</h3>
  </article>

  <article class="card card--grey" style="left:514px;top:0;width:225px;height:266px">
    <div class="photo wood-warm" style="top:0;height:202px" role="img" aria-label="Photo of a fitter marking oak floor boards"></div>
    <h3 class="heading" style="top:211px">Ceariosam volum</h3>
    <p class="copy" style="top:236px">As niam nimaximostia venihitat.<br>Harchictis intiore hentotate venet estem harunt dignis nobit aute libus nonsequis si voluptatia cuptae et aut essum nihic</p>
  </article>
  <article class="card card--grey" style="left:514px;top:274px;width:225px;height:257px">
    <div class="photo wood-roll" style="top:12px;height:169px" role="img" aria-label="Photo of a fitter laying a vinyl wood-effect floor"></div>
    <h3 class="heading" style="top:188px">Ceariosam volum</h3>
    <p class="copy" style="top:212px">As niam nimaximostia venihitat.<br>Harchictis intiore hentotate venet estem harunt dignis nobit aute libus nonsequis si voluptatia cuptae et aut essum nihic</p>
  </article>
</section>

</body>
</html>
```